Business card por a urban DJ, up scale audience target

Need a sober design, modern, conservative colors but i can consider some options, y play rnb, hip hop, EDM and top40.

Business card for contact and personal info, double sided, use logo attrached please; im 42 so i need a card acording to my age an target audience.

Target Market(s)

Adult people, up scale audience

Industry/Entity Type

Music Download

Contact Information for Business Card

Cel (318) 4207265518 www.lumadrift.com

Requirements
Must have
• open mind
Nice to have
• open mind
Should not have
• DJ

```html
<!DOCTYPE html>
<html lang="en">
<head>
<meta charset="utf-8">
<title>Lumadrift Business Card</title>
<link href="https://fonts.googleapis.com/css2?family=Open+Sans:wght@400;700&display=swap" rel="stylesheet">
<style>
  :root {
    --backdrop: #2a2a2a;
    --card-dark: #0b0b0b;
    --card-dark-sheen: #1c1c1c;
    --card-light: #f7f7f7;
    --card-light-sheen: #e6e6e6;
    --ink-dark: #222222;
    --ink-light: #ffffff;
  }
  html, body {
    margin: 0;
    padding: 0;
    width: 1200px;
    height: 1189px;
    overflow: hidden;
    background: var(--backdrop);
    font-family: "Open Sans", Arial, sans-serif;
  }
  .canvas {
    position: relative;
    width: 1200px;
    height: 1189px;
  }
  .card {
    position: absolute;
    left: 160px;
    width: 880px;
    height: 503px;
    overflow: hidden;
    box-shadow: 0 18px 40px rgba(0, 0, 0, 0.45);
  }
  .card-front { top: 60px; background: var(--card-dark); }
  .card-back { top: 626px; background: var(--card-light); }
  .pattern-layer {
    position: absolute;
    inset: 0;
  }
  .card-front .pattern-layer {
    background: linear-gradient(135deg, var(--card-dark-sheen) 0%, var(--card-dark) 55%, var(--card-dark-sheen) 100%);
  }
  .card-back .pattern-layer {
    background: linear-gradient(135deg, var(--card-light) 0%, var(--card-light-sheen) 50%, var(--card-light) 100%);
  }
  .brand-name {
    position: absolute;
    font-weight: 700;
    letter-spacing: 4px;
    line-height: 1;
  }
  .card-front .brand-name {
    left: 0;
    right: 0;
    top: 190px;
    text-align: center;
    font-size: 130px;
    color: var(--ink-light);
  }
  .card-back .brand-name {
    left: 70px;
    top: 230px;
    font-size: 92px;
    color: var(--ink-dark);
  }
  .contact-block {
    position: absolute;
    left: 500px;
    top: 150px;
    color: var(--ink-dark);
  }
  .contact-name {
    font-size: 34px;
    font-weight: 400;
    letter-spacing: 1px;
    margin: 0 0 4px;
  }
  .contact-line {
    font-size: 25px;
    margin: 0;
    line-height: 1.25;
  }
</style>
</head>
<body>
  <main class="canvas">
    <section class="card card-front">
      <div class="pattern-layer" role="img" aria-label="Dark faceted diamond pattern background"></div>
      <div class="brand-name">LUMA</div>
    </section>
    <section class="card card-back">
      <div class="pattern-layer" role="img" aria-label="Light faceted diamond pattern background"></div>
      <div class="brand-name">LUMA</div>
      <div class="contact-block">
        <p class="contact-name">JONATHAN DOE</p>
        <p class="contact-line">Managing Director</p>
        <p class="contact-line">(318) 4207265518</p>
        <p class="contact-line">www.lumadrift.com</p>
      </div>
    </section>
  </main>
</body>
</html>
```